Stationery Design Project for Marketing Consultancy

I have started a new consultancy business and require the following elements to be designed using existing logo:
• Business card
• Letterhead
• Envelope (DL, C4, C5)
• Microsoft word template for report writing
• A4 Presentation Folder
• Powerpoint template
COPY FOR FRONT AND BACK OF BUSINESS CARD
logo
'Measurable Marketing. Epic Results' slogan (but no need to use existing lockup with logo)
name, B Bus. Mktg, Grad Dip Digital Mktg, CPM (post nominal abbreviations in smaller font)
mobile: 04XX-XXX-XXX (I will give details to the winner to add)
website: www.tolvarin.com.au
email: info@tolvarin.com.au
COPY FOR LETTERHEAD
Logo
Company Name
Please, submit your designs that include business card, letterhead and envelope. Once selected the winner will be asked to complete the project by creating the rest of the artwork.
FINAL FILES
Print ready files to be supplied as well as Indesign files so that minor amends can be made if necessary in future.
• Layered vectors in EPS & PDF
• Screen quality JPEG & PNGs
ABOUT THE BUSINESS: TOLVARIN
I work with clients to understand their business challenges, developing and executing measurable marketing strategies tied to key business metrics. Services include:
Services include:
• Business planning and business development
• Marketing and brand strategy
• Insight-driven integrated campaigns
• Loyalty programs and retention marketing
• Marketing automation
• Direct marketing (traditional and digital)
• Content strategy and development
Hi everyone,
Target Market(s)
Corporate decision makers (heads of marketing, general managers etc) and small to medium sized business owners. Predominately male aged 35+
Industry/Entity Type
Marketing
Requirements
Must have
- BRAND PERSONALITY
The successful design will communicate brand personality. I am a professional, results-driven entrepreneur, but want to show off my creative flair.
MEMORABILITY
Looking for a unique and eye-catching design. Am considering special printing effects (die cuts, letterpress, interactive elements, embossing, foiling etc) or a striking minimalist approach.
Nice to have
- I have a mission that could be incorporated on reverse if room -
Turning insights into actions & passion into profit.
Should not have
- Use of pink or green.

```html
<!DOCTYPE html>
<html lang="en">
<head>
<meta charset="utf-8">
<title>Tolvarin Business Card</title>
<link href="https://fonts.googleapis.com/css2?family=Source+Sans+3:wght@400;600&display=swap" rel="stylesheet">
<style>
:root{
  --page:#ffffff;
  --brand-orange:#ff4800;
  --card-grey:#f1f1f1;
  --card-dark-top:#262626;
  --card-dark-bottom:#1c1c1c;
  --ink:#111111;
  --paper-text:#f2f2f2;
  --accent-text:#e8561e;
}
*{margin:0;padding:0;box-sizing:border-box}
html,body{width:1200px;height:907px;overflow:hidden;background:var(--page)}
body{position:relative;font-family:"Source Sans 3",sans-serif}

.card{position:absolute;left:301px;width:618px;height:363px}
.card-front{top:88px;display:flex}
.card-back{top:498px;background:linear-gradient(180deg,var(--card-dark-top),var(--card-dark-bottom));color:var(--paper-text)}

.front-brand{width:363px;height:100%;background:var(--brand-orange);position:relative}
.brand-wordmark{position:absolute;left:0;right:0;top:218px;text-align:center;font-size:48px;font-weight:600;letter-spacing:2px;color:var(--ink);line-height:1}
.brand-dot{position:absolute;left:160px;top:112px;width:44px;height:44px;border-radius:50%;background:var(--ink)}

.front-slogan{flex:1;background:var(--card-grey);position:relative;color:var(--ink)}
.slogan-lead{position:absolute;left:33px;top:222px;font-size:17px;line-height:1}
.slogan-punch{position:absolute;left:33px;top:251px;font-size:26px;letter-spacing:1px;line-height:1}

.holder-name{position:absolute;left:52px;top:148px;font-size:17px;line-height:1;color:var(--accent-text)}
.holder-name .given{font-weight:600}
.holder-credentials{position:absolute;left:52px;top:174px;font-size:11px;line-height:1}
.contact-list{position:absolute;left:52px;top:213px;list-style:none;font-size:17px;line-height:23px}
.contact-list .label{display:inline-block;width:24px;color:var(--accent-text);font-weight:600}

.back-brand{position:absolute;left:340px;top:128px;width:210px;text-align:center;font-size:30px;font-weight:600;letter-spacing:2px;line-height:1;color:var(--paper-text)}
.mission{position:absolute;left:341px;top:236px;font-size:16px;line-height:23px}
.mission .second{font-size:17px}
</style>
</head>
<body>
  <section class="card card-front">
    <div class="front-brand">
      <span class="brand-dot"></span>
      <p class="brand-wordmark">TOLVARIN</p>
    </div>
    <div class="front-slogan">
      <p class="slogan-lead">Measurable Marketing.</p>
      <p class="slogan-punch">Epic Results.</p>
    </div>
  </section>

  <section class="card card-back">
    <p class="holder-name"><span class="given">Liam</span> Harrow</p>
    <p class="holder-credentials">B Bus. Mktg, Grad Dip Digital Mktg, CPM</p>
    <ul class="contact-list">
      <li><span class="label">M</span>0400 555 018</li>
      <li><span class="label">W</span>www.tolvarin.com.au</li>
      <li><span class="label">E</span>info@tolvarin.com.au</li>
    </ul>
    <p class="back-brand">TOLVARIN</p>
    <p class="mission">Turning insights into action<br><span class="second">and passion into profit.</span></p>
  </section>
</body>
</html>
```